Marrowind Apiary Annual Poster Design

We are beekeepers in the beach town of Santa Barbara, California. Love Art Deco posters. Would like to release one annually. We are opening two stores, one in Santa Barbara and one in Carpinteria. We have a bee in our logo but does not have to be that bee. WE DO NOT LIKE CARTOON BEES. There is alot potential here with bees, surf culture, beach culture, We are on the coast with amazing sunsets, palm trees, etc.

```html
<!DOCTYPE html>
<html lang="en">
<head>
<meta charset="utf-8">
<title>Marrowind Apiary – Bee Keepers in California Poster</title>
<link href="https://fonts.googleapis.com/css2?family=Alfa+Slab+One&family=Bebas+Neue&family=Poppins:wght@400;500;600&display=swap" rel="stylesheet">
<style>
  :root {
    --honey: #fbb41c;
    --honey-deep: #f2a612;
    --slate: #3e524e;
    --slate-dark: #34463f;
    --slate-light: #4b605b;
    --pale-green: #c3cf7e;
    --pale-yellow: #f1e98a;
    --white: #ffffff;
    --ink: #2f3a30;
    --bee-brown: #4a2a14;
    --bee-yellow: #e2b21c;
    --ghost: #6f8a7c;
    --olive: #8e9a5f;
    --page: #ffffff;
  }
  * { margin: 0; padding: 0; box-sizing: border-box; }
  html, body { width: 1200px; height: 2400px; overflow: hidden; background: var(--page); }
  .canvas { position: relative; width: 1200px; height: 2400px; }

  .poster {
    position: absolute; left: 50px; top: 466px;
    width: 1100px; height: 1468px;
    background: var(--honey);
  }
  .poster__panel {
    position: absolute; left: 21px; top: 28px; right: 21px; bottom: 22px;
    background: radial-gradient(ellipse at 45% 40%, var(--slate-light) 0%, var(--slate) 55%, var(--slate-dark) 100%);
    overflow: hidden;
  }
  .art { position: absolute; }
  .art--comb-top {
    right: 0; top: 0; width: 265px; height: 185px;
    background: linear-gradient(135deg, var(--honey) 0%, var(--honey-deep) 100%);
    clip-path: polygon(12% 0, 100% 0, 100% 100%, 60% 90%, 25% 60%, 5% 40%);
  }
  .art--comb-bottom {
    left: 0; bottom: 0; width: 185px; height: 92px;
    background: var(--honey);
    clip-path: polygon(0 20%, 45% 0, 80% 35%, 100% 100%, 0 100%);
  }
  .art--bee-small {
    left: 777px; top: 125px; width: 264px; height: 230px;
    background: radial-gradient(ellipse at center, rgba(150,175,150,0.55) 0%, rgba(111,138,124,0.25) 60%, transparent 75%);
  }
  .art--bee-ghost {
    left: 223px; top: 710px; width: 580px; height: 420px;
    background: radial-gradient(ellipse at center, rgba(111,138,124,0.45) 0%, rgba(111,138,124,0.15) 55%, transparent 72%);
  }
  .art--bee-large {
    left: 305px; top: 786px; width: 774px; height: 654px;
    background:
      radial-gradient(ellipse at 75% 20%, rgba(220,214,196,0.9) 0%, rgba(220,214,196,0.6) 28%, transparent 45%),
      radial-gradient(ellipse at 40% 45%, var(--bee-yellow) 0%, #c7931a 35%, var(--bee-brown) 70%, transparent 78%);
  }

  .headline { position: absolute; left: 41px; display: block; overflow: visible; }
  .headline--bee { top: 32px; }
  .headline--keepers { top: 358px; }
  .headline text.bee-word { font-family: "Alfa Slab One", Georgia, serif; }
  .headline text.keepers-word { font-family: "Bebas Neue", "Oswald", sans-serif; }

  .region {
    position: absolute; left: 39px; top: 553px;
    font-family: "Poppins", Arial, sans-serif; font-weight: 400;
    font-size: 92px; line-height: 1; color: var(--white);
    letter-spacing: -0.5px; white-space: nowrap;
  }

  .web-bar {
    position: absolute; left: 35px; top: 648px; width: 597px; height: 41px;
    background: var(--honey);
    font-family: "Poppins", Arial, sans-serif; font-weight: 500;
    font-size: 25px; letter-spacing: 4.6px; color: var(--ink);
    display: flex; align-items: center; justify-content: center;
  }

  .opening {
    position: absolute; left: 665px; top: 274px; height: 341px;
    border-left: 2px solid var(--pale-green);
    padding-left: 16px;
    font-family: "Poppins", Arial, sans-serif; color: var(--white);
  }
  .opening__title {
    font-family: "Bebas Neue", "Oswald", sans-serif;
    font-size: 82px; line-height: 0.9; color: var(--honey);
    letter-spacing: -0.5px; margin-top: -4px;
  }
  .opening__store { margin-top: 18px; }
  .opening__store + .opening__store { margin-top: 14px; }
  .opening__name { font-size: 56px; line-height: 1.02; font-weight: 400; }
  .pin { display: block; }

  .brand {
    position: absolute; left: 34px; top: 737px; width: 279px; height: 279px;
    border-radius: 50%;
    background: var(--olive);
    display: flex; align-items: center; justify-content: center; text-align: center;
    font-family: "Poppins", Arial, sans-serif; font-weight: 500;
    font-size: 34px; line-height: 1.15; color: var(--white);
  }

  .locations {
    position: absolute; left: 24px; top: 1040px;
    font-family: "Poppins", Arial, sans-serif;
  }
  .locations__title {
    font-weight: 600; font-size: 26px; line-height: 1.22;
    color: var(--honey); text-transform: uppercase; margin-bottom: 12px;
  }
  .locations__list { list-style: none; }
  .locations__item {
    display: flex; align-items: center; gap: 10px;
    font-size: 26px; line-height: 33px; color: var(--white);
  }
</style>
</head>
<body>
<div class="canvas">
  <section class="poster" aria-label="Marrowind Apiary opening poster">
    <div class="poster__panel">

      <div class="art art--comb-top" role="img" aria-label="Golden honeycomb cells in the corner"></div>
      <div class="art art--bee-small" role="img" aria-label="Faint etched honeybee in flight"></div>
      <div class="art art--bee-ghost" role="img" aria-label="Faded etched bee in the background"></div>
      <div class="art art--bee-large" role="img" aria-label="Large etched honeybee illustration in yellow and brown"></div>
      <div class="art art--comb-bottom" role="img" aria-label="Golden honeycomb cells in the corner"></div>

      <svg class="headline headline--bee" width="600" height="320" viewBox="0 0 600 320" aria-label="Bee">
        <text class="bee-word" x="0" y="308" font-size="395" textLength="596" lengthAdjust="spacingAndGlyphs" fill="var(--pale-green)">BEE</text>
      </svg>

      <svg class="headline headline--keepers" width="600" height="180" viewBox="0 0 600 180" aria-label="Keepers">
        <defs>
          <linearGradient id="keepers-fill" x1="0" y1="0" x2="1" y2="1">
            <stop offset="0" stop-color="var(--pale-yellow)"/>
            <stop offset="1" stop-color="var(--pale-green)"/>
          </linearGradient>
        </defs>
        <text class="keepers-word" x="0" y="185" font-size="222" textLength="598" lengthAdjust="spacingAndGlyphs" fill="url(#keepers-fill)">KEEPERS</text>
      </svg>

      <div class="region">IN CALIFORNIA</div>

      <div class="web-bar">www.marrowindapiary.com</div>

      <div class="opening">
        <div class="opening__title">OPENING</div>
        <div class="opening__store">
          <svg class="pin" width="24" height="30" viewBox="0 0 24 30" aria-hidden="true">
            <path d="M12 1C6 1 1.5 5.5 1.5 11.2 1.5 18.5 12 29 12 29s10.5-10.5 10.5-17.8C22.5 5.5 18 1 12 1z" fill="var(--pale-green)"/>
            <circle cx="12" cy="11" r="4.5" fill="var(--slate)"/>
          </svg>
          <div class="opening__name">Santa<br>Barbara</div>
        </div>
        <div class="opening__store">
          <svg class="pin" width="24" height="30" viewBox="0 0 24 30" aria-hidden="true">
            <path d="M12 1C6 1 1.5 5.5 1.5 11.2 1.5 18.5 12 29 12 29s10.5-10.5 10.5-17.8C22.5 5.5 18 1 12 1z" fill="var(--pale-green)"/>
            <circle cx="12" cy="11" r="4.5" fill="var(--slate)"/>
          </svg>
          <div class="opening__name">Carpinteria</div>
        </div>
      </div>

      <div class="brand">Marrowind<br>Apiary</div>

      <div class="locations">
        <div class="locations__title">Other<br>Locations</div>
        <ul class="locations__list">
          <li class="locations__item"><svg width="11" height="14" viewBox="0 0 24 30" aria-hidden="true"><path d="M12 1C6 1 1.5 5.5 1.5 11.2 1.5 18.5 12 29 12 29s10.5-10.5 10.5-17.8C22.5 5.5 18 1 12 1z" fill="var(--pale-green)"/><circle cx="12" cy="11" r="5" fill="var(--slate)"/></svg>Santa Ynez, CA</li>
          <li class="locations__item"><svg width="11" height="14" viewBox="0 0 24 30" aria-hidden="true"><path d="M12 1C6 1 1.5 5.5 1.5 11.2 1.5 18.5 12 29 12 29s10.5-10.5 10.5-17.8C22.5 5.5 18 1 12 1z" fill="var(--pale-green)"/><circle cx="12" cy="11" r="5" fill="var(--slate)"/></svg>Ventura, CA</li>
          <li class="locations__item"><svg width="11" height="14" viewBox="0 0 24 30" aria-hidden="true"><path d="M12 1C6 1 1.5 5.5 1.5 11.2 1.5 18.5 12 29 12 29s10.5-10.5 10.5-17.8C22.5 5.5 18 1 12 1z" fill="var(--pale-green)"/><circle cx="12" cy="11" r="5" fill="var(--slate)"/></svg>Santa Barbara, CA</li>
          <li class="locations__item"><svg width="11" height="14" viewBox="0 0 24 30" aria-hidden="true"><path d="M12 1C6 1 1.5 5.5 1.5 11.2 1.5 18.5 12 29 12 29s10.5-10.5 10.5-17.8C22.5 5.5 18 1 12 1z" fill="var(--pale-green)"/><circle cx="12" cy="11" r="5" fill="var(--slate)"/></svg>Montecito, CA</li>
          <li class="locations__item"><svg width="11" height="14" viewBox="0 0 24 30" aria-hidden="true"><path d="M12 1C6 1 1.5 5.5 1.5 11.2 1.5 18.5 12 29 12 29s10.5-10.5 10.5-17.8C22.5 5.5 18 1 12 1z" fill="var(--pale-green)"/><circle cx="12" cy="11" r="5" fill="var(--slate)"/></svg>Ojai, CA</li>
          <li class="locations__item"><svg width="11" height="14" viewBox="0 0 24 30" aria-hidden="true"><path d="M12 1C6 1 1.5 5.5 1.5 11.2 1.5 18.5 12 29 12 29s10.5-10.5 10.5-17.8C22.5 5.5 18 1 12 1z" fill="var(--pale-green)"/><circle cx="12" cy="11" r="5" fill="var(--slate)"/></svg>Carpinteria, CA</li>
        </ul>
      </div>

    </div>
  </section>
</div>
</body>
</html>
```